Business Card Design

New business, starting out small. High end residential/ commercial building company in Sydney Australia's prestigious Eastern suburbs, perfection is our motto and we want our marketing design to reflect that.

Therefore marketing towards high end clients. Looking for design concepts that will portray this image and will appeal to both male and females, prototype has been included- see images. Although we are open to ideas we have included this to give direction.

DARK Navy and white is the colour scheme, as per image provided. Logo ideas welcomed, however design is preferred simple, modern and sophisticated.

This business card will be the template and inspiration for website, t-shirt, banners etc to come so if you want the business, show us your design!

Contact Information for Business Card

Company name: Ardent Frame Building
Catch phrase: Built with intent
Owner/operator: Lucas Penrith
Phone: 0458219604
Website: www.ardentframebuilding.com.au
Licence No 518204K
ABN 72 913 058
Email address
(displayed on back of card):info@ardentframebuilding.com.au

```html
<!DOCTYPE html>
<html lang="en">
<head>
<meta charset="utf-8">
<title>Ardent Frame Building — Business Card</title>
<link rel="stylesheet" href="https://fonts.googleapis.com/css2?family=Josefin+Sans:wght@300;400&display=swap">
<style>
  :root {
    --navy: #0d1f36;
    --navy-mid: #16304d;
    --navy-deep: #08162a;
    --paper: #ffffff;
    --ink: #1a1a1a;
    --ink-soft: #cfd6df;
    --stage: #e9e9eb;
  }
  * { box-sizing: border-box; margin: 0; padding: 0; }
  html, body { width: 1200px; height: 1000px; overflow: hidden; }
  body {
    background: var(--stage);
    font-family: "Josefin Sans", sans-serif;
    position: relative;
  }
  .card {
    position: absolute;
    left: 285px;
    width: 630px;
    height: 360px;
    box-shadow: 0 10px 30px rgba(0,0,0,0.18);
    overflow: hidden;
  }
  .card--front {
    top: 110px;
    background: linear-gradient(135deg, var(--navy) 0%, var(--navy-mid) 55%, var(--navy-deep) 100%);
    color: var(--paper);
  }
  .card--back {
    top: 530px;
    background: var(--paper);
    color: var(--ink);
  }
  .corner-fold {
    position: absolute;
    top: 0; left: 0;
  }
  .owner {
    position: absolute;
    top: 46px; left: 52px;
    font-weight: 300;
    font-size: 15px;
    letter-spacing: 0.5px;
  }
  .owner .role { font-size: 11px; }
  .wordmark {
    position: absolute;
    top: 148px; left: 0; right: 0;
    text-align: center;
  }
  .company {
    font-weight: 400;
    font-size: 20px;
    letter-spacing: 3px;
    text-transform: uppercase;
  }
  .tagline {
    margin-top: 12px;
    font-weight: 300;
    font-size: 13px;
    letter-spacing: 1px;
    color: var(--ink-soft);
  }
  .contact {
    position: absolute;
    right: 34px; bottom: 34px;
    list-style: none;
    text-align: right;
    font-weight: 300;
    font-size: 12px;
    letter-spacing: 0.8px;
    line-height: 24px;
    color: var(--ink-soft);
  }
  .contact li { display: flex; justify-content: flex-end; align-items: center; gap: 8px; }
  .contact .phone { font-size: 14px; letter-spacing: 1.5px; }
  .contact .icon { width: 14px; height: 14px; }
  .contact .legal { padding-right: 22px; }
  .email {
    position: absolute;
    right: 44px; bottom: 56px;
    font-size: 13px;
    letter-spacing: 2.5px;
  }
</style>
</head>
<body>
  <section class="card card--front" aria-label="Business card front">
    <svg class="corner-fold" width="46" height="46" viewBox="0 0 46 46" aria-hidden="true">
      <polygon points="0,0 46,0 0,46" fill="#ffffff"/>
    </svg>
    <p class="owner">Lucas Penrith <span class="role">| Owner/operator</span></p>
    <div class="wordmark">
      <h1 class="company">Ardent Frame Building</h1>
      <p class="tagline">Built with intent</p>
    </div>
    <ul class="contact">
      <li class="phone">0458219604
        <svg class="icon" viewBox="0 0 16 16" aria-hidden="true">
          <path d="M1 5c0-2 3-3 7-3s7 1 7 3v1h-3V5H4v1H1z M3 8h10l1 6H2z" fill="#ffffff"/>
          <circle cx="8" cy="11" r="1.6" fill="#0d1f36"/>
        </svg>
      </li>
      <li>www.ardentframebuilding.com.au
        <svg class="icon" viewBox="0 0 16 16" aria-hidden="true">
          <circle cx="8" cy="8" r="6.5" fill="none" stroke="#cfd6df" stroke-width="1.2"/>
          <ellipse cx="8" cy="8" rx="2.8" ry="6.5" fill="none" stroke="#cfd6df" stroke-width="1"/>
          <line x1="1.5" y1="8" x2="14.5" y2="8" stroke="#cfd6df" stroke-width="1"/>
        </svg>
      </li>
      <li class="legal">Licence No 518204K ABN 72 913 058</li>
    </ul>
  </section>

  <section class="card card--back" aria-label="Business card back">
    <p class="email">info@ardentframebuilding.com.au</p>
  </section>
</body>
</html>
```